Electrician Letterhead Design MVR

We need some letterhead for our bills and other papers.
Customer address is on the right side (Swiss format)
A4 format

Design should also be applicable on Cards

Target Market(s)

Private Customers, Small Business

Industry/Entity Type

Electrician

Other font styles liked:
• incised 901

Colors
00AB8E
00BBA5
67D7C9
C6EFE9
E9F9F6

```html
<!DOCTYPE html>
<html lang="en">
<head>
<meta charset="utf-8">
<title>MVR Letterhead</title>
<link rel="stylesheet" href="https://fonts.googleapis.com/css2?family=Lato:wght@400;700;900&family=Italianno&display=swap">
<style>
  :root {
    --teal-dark: #00AB8E;
    --teal: #00BBA5;
    --teal-light: #67D7C9;
    --teal-pale: #C6EFE9;
    --teal-mist: #E9F9F6;
    --ink: #2b2b2b;
    --paper: #ffffff;
    --backdrop: #e4e6e6;
  }
  * { margin: 0; padding: 0; box-sizing: border-box; }
  html, body {
    width: 1200px; height: 1200px; overflow: hidden;
    background: var(--backdrop);
    font-family: "Lato", sans-serif;
    color: var(--ink);
  }
  .letterhead {
    position: absolute; left: 214px; top: 40px;
    width: 772px; height: 1120px;
    background: var(--paper);
    box-shadow: 0 4px 18px rgba(0,0,0,0.18);
    overflow: hidden;
  }
  .brand { position: absolute; left: 60px; top: 42px; }
  .brand-name {
    display: flex; align-items: center; gap: 10px;
    font-weight: 900; font-size: 62px; line-height: 1;
    letter-spacing: 1px; color: var(--teal-dark);
  }
  .brand-mark {
    width: 16px; height: 16px; border-radius: 50%;
    background: var(--teal-dark);
  }
  .brand-tagline {
    margin-top: 6px; font-size: 11.5px; font-weight: 700;
    color: var(--ink); letter-spacing: 0.2px;
  }
  .contact {
    position: absolute; left: 527px; top: 42px;
    padding-left: 10px; border-left: 1.5px solid var(--teal-dark);
    font-size: 13px; line-height: 18px; font-style: normal;
  }
  .contact .address { margin-bottom: 6px; }
  .contact-line { display: flex; align-items: center; gap: 6px; }
  .contact-line svg { width: 10px; height: 10px; fill: var(--teal-dark); flex: none; }

  .letter {
    position: absolute; left: 60px; top: 248px; width: 653px;
    font-size: 14px; line-height: 18px;
  }
  .letter-top {
    display: flex; justify-content: space-between; align-items: flex-start;
    margin-bottom: 22px;
  }
  .date { font-size: 15px; line-height: 18px; }
  .recipient {
    width: 186px; font-style: normal;
  }
  .recipient p + p { margin-top: 18px; }
  .salutation { font-size: 18px; font-weight: 700; margin-bottom: 18px; }
  .body p {
    text-align: justify; margin-bottom: 18px;
    font-size: 14px; line-height: 17.5px; letter-spacing: 0.1px;
  }
  .closing { margin-top: 38px; }
  .signature {
    font-family: "Italianno", cursive;
    font-size: 46px; line-height: 1; margin-top: 18px; color: #1e1e1e;
  }
  .footer-band { position: absolute; left: 0; bottom: 0; width: 772px; height: 52px; }
</style>
</head>
<body>
  <main class="letterhead">
    <header>
      <div class="brand">
        <div class="brand-name"><span>MVR</span><span class="brand-mark"></span></div>
        <div class="brand-tagline">Elektrotechnik Vogel GmbH</div>
      </div>
      <address class="contact">
        <div class="address">42-07 Linden Way 9,<br>Fairhaven, NY 11204</div>
        <div class="contact-line">
          <svg viewBox="0 0 10 10"><path d="M2 0.5 L4 2.5 L3 3.8 Q4.5 6 6.2 7 L7.5 6 L9.5 8 L8 9.5 Q3.5 9 0.5 2 Z"/></svg>
          <span>555-310-2748</span>
        </div>
        <div class="contact-line">
          <svg viewBox="0 0 10 10"><path d="M0.5 2 H9.5 V8.5 H0.5 Z M1 2.5 L5 5.5 L9 2.5" fill="var(--teal-dark)" stroke="#fff" stroke-width="0.8"/></svg>
          <span>info@examplemail.com</span>
        </div>
        <div class="contact-line">
          <svg viewBox="0 0 10 10"><circle cx="5" cy="5" r="4.5"/><path d="M0.5 5 H9.5 M5 0.5 Q2 5 5 9.5 M5 0.5 Q8 5 5 9.5" stroke="#fff" stroke-width="0.7" fill="none"/></svg>
          <span>www.examplewebsite.com</span>
        </div>
      </address>
    </header>

    <section class="letter">
      <div class="letter-top">
        <p class="date">Feb-03-2022</p>
        <address class="recipient">
          <p>Mr, John Doe<br>President</p>
          <p>Northfield Corporation<br>123 Street Name, Suite# 10<br>City, State, 120023</p>
        </address>
      </div>
      <p class="salutation">Dear Mr, John</p>
      <div class="body">
        <p>Lorem ipsum dolor sit amet, consectetur adipisicing elit, sed do eiusmod tempor incididunt ut labore et dolore magna aliqua. Ut enim ad minim veniam, quis nostrud exercitation ullamco laboris nisi ut aliquip ex ea commodo consequat. Duis aute irure dolor in reprehenderit in voluptate velit esse cillum dolore eu fugiat nulla pariatur.</p>
        <p>Lorem ipsum dolor sit amet, consectetur adipisicing elit, sed do eiusmod tempor incididunt ut labore et dolore magna aliqua. Ut enim ad minim veniam, quis nostrud exercitation ullamco laboris nisi ut aliquip ex ea commodo consequat. Duis aute irure dolor in reprehenderit in voluptate velit esse cillum dolore eu fugiat nulla pariatur.</p>
        <p>Lorem ipsum dolor sit amet, consectetur adipisicing elit, sed do eiusmod tempor incididunt ut labore et dolore magna aliqua. Ut enim ad minim veniam, quis nostrud exercitation ullamco laboris nisi ut aliquip ex ea commodo consequat.</p>
        <p>Excepteur sint occaecat cupidatat non proident, sunt in culpa qui officia deserunt mollit anim id est laborum. re et dolore magnam aliquam quaerat voluptatem.</p>
      </div>
      <p class="closing">Regards</p>
      <p class="signature">Daniel Hart</p>
    </section>

    <svg class="footer-band" viewBox="0 0 772 52" preserveAspectRatio="none" aria-hidden="true">
      <polygon points="0,10 533,10 522,24 0,24" fill="var(--teal-light)"/>
      <polygon points="545,24 577,0 772,0 772,52 0,52 0,28 540,28" fill="var(--teal-dark)"/>
    </svg>
  </main>
</body>
</html>
```